Corvane Holdings , new business card design

investment firm with corporate clients . need double sided business card , vertical and horizontal options ,logo must be clear. prefer pantone colors only and sharp design. website also www.corvane.ae

Khalid Bin Tarrafi
Managing Director
Tel. +971 4 387 2940
Mobile +971 50 518 2403
khalid@corvane.ae
Q-Span Plaza, officw 18-B07, Warqa Gardens, Dubai

Contact Information for Business Card

Khalid Bin Tarrafi
Managing Director

Font styles to use
Serif

Colors

Designer to choose colors to be used in the design.

```html
<!DOCTYPE html>
<html lang="en">
<head>
<meta charset="utf-8">
<title>Corvane Holdings – Business Card</title>
<link rel="stylesheet" href="https://fonts.googleapis.com/css2?family=Mulish:wght@300;400;700&display=swap">
<style>
  :root {
    --backdrop: #e8e5e2;
    --card: #f7f7f7;
    --brand-blue: #4a7199;
    --swoosh-grey: #cbc8c6;
    --ink: #2a2a2a;
    --on-blue: #ffffff;
    --on-blue-soft: #e6edf5;
  }
  * { margin: 0; padding: 0; box-sizing: border-box; }
  html, body {
    width: 1200px;
    height: 997px;
    overflow: hidden;
    background: var(--backdrop);
    font-family: "Mulish", "Century Gothic", sans-serif;
  }
  .sheet {
    position: relative;
    width: 1200px;
    height: 997px;
  }
  .card {
    position: absolute;
    left: 290px;
    width: 620px;
    height: 354px;
    background: var(--card);
    overflow: hidden;
    box-shadow: 0 2px 6px rgba(0,0,0,0.08);
  }
  .card--front { top: 112px; }
  .card--back  { top: 530px; }

  .card__swoosh {
    position: absolute;
    inset: 0;
    width: 100%;
    height: 100%;
  }

  .wordmark {
    position: absolute;
    display: flex;
    align-items: center;
    gap: 12px;
    color: var(--ink);
    font-weight: 300;
    text-transform: uppercase;
    white-space: nowrap;
  }
  .wordmark__square {
    width: 14px;
    height: 14px;
    background: var(--brand-blue);
    flex: none;
  }
  .card--front .wordmark {
    left: 44px;
    top: 140px;
    font-size: 21px;
    letter-spacing: 5px;
  }
  .card--back .wordmark {
    left: 50%;
    top: 50%;
    transform: translate(-50%, -50%);
    font-size: 28px;
    letter-spacing: 7px;
  }
  .card--back .wordmark__square { width: 18px; height: 18px; }

  .holder {
    position: absolute;
    left: 52px;
    top: 222px;
    color: var(--on-blue);
  }
  .holder__name {
    font-size: 15px;
    font-weight: 700;
    letter-spacing: 0.2px;
  }
  .holder__role {
    font-size: 13px;
    font-weight: 300;
    margin-top: 2px;
  }
  .contact-list {
    list-style: none;
    margin-top: 12px;
  }
  .contact-list li {
    display: flex;
    align-items: center;
    gap: 10px;
    font-size: 13px;
    font-weight: 400;
    line-height: 17px;
    color: var(--on-blue-soft);
  }
  .contact-list svg {
    width: 11px;
    height: 11px;
    flex: none;
  }
  .address {
    position: absolute;
    left: 330px;
    top: 216px;
    font-size: 13px;
    font-weight: 300;
    line-height: 17px;
    color: var(--on-blue-soft);
    font-style: normal;
  }
</style>
</head>
<body>
<main class="sheet">

  <section class="card card--front" aria-label="Business card, contact side">
    <svg class="card__swoosh" viewBox="0 0 620 354" preserveAspectRatio="none" aria-hidden="true">
      <path d="M0,196 Q360,190 606,0 L620,0 L620,14 Q370,212 0,222 Z" fill="var(--swoosh-grey)"/>
      <path d="M30,188 Q370,176 588,0" fill="none" stroke="var(--swoosh-grey)" stroke-width="1.5"/>
      <path d="M0,222 Q370,212 620,14 L620,354 L0,354 Z" fill="var(--brand-blue)"/>
    </svg>

    <div class="wordmark">
      <span class="wordmark__square"></span>
      <span class="wordmark__name">Corvane Holdings</span>
    </div>

    <div class="holder">
      <p class="holder__name">Khalid Bin Tarrafi</p>
      <p class="holder__role">Managing Director</p>
      <ul class="contact-list">
        <li>
          <svg viewBox="0 0 12 12" aria-hidden="true"><path d="M2.5,1 L4.5,1 L5.2,3.4 L4,4.3 Q5,6.6 7.7,8 L8.6,6.8 L11,7.5 L11,9.5 Q10.5,11 9,11 Q1,10 1,2.5 Q1,1 2.5,1 Z" fill="none" stroke="currentColor" stroke-width="1"/></svg>
          <span>+971 50 518 2403</span>
        </li>
        <li>
          <svg viewBox="0 0 12 12" aria-hidden="true"><rect x="3" y="0.8" width="6" height="10.4" rx="1" fill="none" stroke="currentColor" stroke-width="1"/><circle cx="6" cy="9.4" r="0.6" fill="currentColor"/></svg>
          <span>+971 50 518 2403</span>
        </li>
        <li>
          <svg viewBox="0 0 12 12" aria-hidden="true"><rect x="0.8" y="2.3" width="10.4" height="7.4" fill="none" stroke="currentColor" stroke-width="1"/><path d="M0.8,2.3 L6,6.5 L11.2,2.3" fill="none" stroke="currentColor" stroke-width="1"/></svg>
          <span>khalid@corvane.ae</span>
        </li>
      </ul>
    </div>

    <address class="address">
      Q-Span Plaza, officw 18-B07,<br>
      Warqa Gardens, Dubai
    </address>
  </section>

  <section class="card card--back" aria-label="Business card, logo side">
    <div class="wordmark">
      <span class="wordmark__square"></span>
      <span class="wordmark__name">Corvane Holdings</span>
    </div>
  </section>

</main>
</body>
</html>
```